Maplecrest Disability - Social Security Disability Attorneys

Our company is expanding to attract clients nationwide for our social security disability practice. We have a logo, but I am looking for a creative and elegant letterhead that projects an image of being technologically advanced but still professional enough for the legal field. I am looking for the "wow factor" combined with this is still professional enough for a law practice.

Requesting letterhead and business card design
Updates

Had to update and change the logo. The previous logo had a typo. Please send updates with the new logo for consideration. The letterhead and business cards should be professional enough to be used for a law firm. Thanks.

Industry/Entity Type

Law Practice, Law Firm, Healthcare Industry, Government

Colors

Designer to choose colors to be used in the design.

Requirements
Nice to have
• **Please create a vertical design for the business card**

```html
<!DOCTYPE html>
<html lang="en">
<head>
<meta charset="utf-8">
<title>Maplecrest Disability – Business Card</title>
<link rel="stylesheet" href="https://fonts.googleapis.com/css2?family=Cinzel:wght@400;500;600&family=Varela+Round&display=swap">
<style>
  :root {
    --page-bg: #b3b3b3;
    --card-white: #f5f6f7;
    --brand-blue: #0a63dd;
    --brand-blue-light: #0a9ae0;
    --brand-blue-deep: #0552d6;
    --accent-orange: #ea7a0c;
    --text-white: #ffffff;
  }
  * { margin: 0; padding: 0; box-sizing: border-box; }
  html, body {
    width: 1200px; height: 1200px; overflow: hidden;
    background: var(--page-bg);
  }
  .stage {
    position: absolute; left: 0; top: 0;
    width: 1400px; height: 1400px;
    transform: scale(0.857143); transform-origin: 0 0;
  }
  .card {
    position: absolute; left: 306px;
    width: 800px; height: 457px;
    border-radius: 28px; overflow: hidden;
  }
  .card-front { top: 193px; background: var(--card-white); }
  .card-back {
    top: 762px;
    background: radial-gradient(ellipse 60% 70% at 50% 45%, var(--brand-blue-light) 0%, var(--brand-blue) 70%, var(--brand-blue-deep) 100%);
  }
  .wave { position: absolute; inset: 0; width: 800px; height: 457px; }

  .wordmark {
    position: absolute; left: 48px; top: 134px;
    font-family: "Cinzel", serif; font-weight: 500;
    font-size: 33px; color: var(--brand-blue); letter-spacing: 0.01em;
    white-space: nowrap;
  }

  .contact {
    position: absolute; right: 44px; top: 222px;
    text-align: right; color: var(--text-white);
    font-family: "Varela Round", sans-serif; font-size: 16.5px; line-height: 22px;
  }
  .contact-name {
    font-family: "Cinzel", serif; font-weight: 600; font-size: 24px;
    line-height: 28px; letter-spacing: 0.01em; white-space: nowrap;
  }
  .contact-title { margin-bottom: 8px; }
  .contact-address { margin-bottom: 12px; }
  .contact-line { display: flex; justify-content: flex-end; align-items: center; gap: 8px; }
  .contact-line svg { width: 18px; height: 18px; flex: none; }

  .back-title {
    position: absolute; left: 0; right: 0; top: 56px;
    text-align: center; color: var(--text-white);
    font-family: "Cinzel", serif; font-weight: 500; font-size: 46px; letter-spacing: 0.01em;
  }
  .back-url {
    position: absolute; left: 0; right: 0; top: 117px;
    text-align: center; color: var(--text-white);
    font-family: "Varela Round", sans-serif; font-size: 16px; letter-spacing: 0.62em;
  }
</style>
</head>
<body>
<div class="stage">

  <section class="card card-front">
    <svg class="wave" viewBox="0 0 800 457" aria-hidden="true">
      <defs>
        <linearGradient id="waveFill" x1="0" y1="0" x2="1" y2="0">
          <stop offset="0" stop-color="#0a63dd"/>
          <stop offset="0.5" stop-color="#0a95e0"/>
          <stop offset="1" stop-color="#0a63dd"/>
        </linearGradient>
      </defs>
      <path d="M0,340 C80,380 150,408 230,405 C330,400 420,290 500,215 C580,140 650,100 720,108 C760,112 780,118 800,125 L800,457 L0,457 Z" fill="url(#waveFill)"/>
      <path d="M0,308 C80,360 150,398 200,398 C300,398 380,300 450,230 C540,140 610,100 690,92"
            fill="none" stroke="var(--accent-orange)" stroke-width="15" stroke-linecap="round"/>
      <path d="M215,404 C315,402 395,305 462,238 C545,155 615,108 700,95"
            fill="none" stroke="var(--brand-blue)" stroke-width="3"/>
      <path d="M228,406 C328,404 408,310 474,244 C556,162 626,113 712,98"
            fill="none" stroke="var(--brand-blue)" stroke-width="2"/>
    </svg>

    <div class="wordmark">MAPLECREST DISABILITY</div>

    <div class="contact">
      <div class="contact-name">DANIEL WHITMORE</div>
      <div class="contact-title">Founder &amp; CEO</div>
      <div class="contact-address">4120 Birchwood Lane<br>Fairbanks, Alaska 99701</div>
      <div class="contact-line">555-214-7380
        <svg viewBox="0 0 24 24" aria-hidden="true"><path fill="#fff" d="M6.6 10.8a15.2 15.2 0 0 0 6.6 6.6l2.2-2.2c.3-.3.7-.4 1-.2 1.1.4 2.3.6 3.6.6.6 0 1 .4 1 1V20c0 .6-.4 1-1 1C10.6 21 3 13.4 3 4c0-.6.4-1 1-1h3.5c.6 0 1 .4 1 1 0 1.3.2 2.5.6 3.6.1.3 0 .7-.2 1z"/></svg>
      </div>
      <div class="contact-line">555-309-6612
        <svg viewBox="0 0 24 24" aria-hidden="true"><rect x="6" y="2" width="12" height="20" rx="2" fill="none" stroke="#fff" stroke-width="2"/><circle cx="12" cy="18.5" r="1" fill="#fff"/></svg>
      </div>
      <div class="contact-line">info@maplecrestdisability.com
        <svg viewBox="0 0 24 24" aria-hidden="true"><rect x="3" y="6" width="18" height="12" fill="#fff"/><path d="M3 6l9 7 9-7" fill="none" stroke="#0a7fe0" stroke-width="1.5"/></svg>
      </div>
      <div class="contact-line">www.maplecrestdisability.com
        <svg viewBox="0 0 24 24" aria-hidden="true"><circle cx="12" cy="12" r="9" fill="#fff"/><path d="M8 7c2 1 3 3 2 5s-3 2-3 4M15 5c-1 2 0 3 2 4s2 3 1 5" fill="none" stroke="#0a7fe0" stroke-width="1.5"/></svg>
      </div>
    </div>
  </section>

  <section class="card card-back">
    <div class="back-title">MAPLECREST DISABILITY</div>
    <div class="back-url">www.MaplecrestDisability.com</div>
  </section>

</div>
</body>
</html>
```